Meridale Bed Company Needs Business Card

Looking for a very nice looking business card. Creative but not extravagant. We sell beds and pillows across the U.S. and need something professional but catchy. I have attached the logo.

Name : Devin Holt
Title : President
Phone : (800) 471-2960
Email: sleep@quilmora.com
Website: www.quilmora.com

Can be single-sided or double-sided
horizontal or vertical

Can use Blues/Greys

Target Market(s)

Mass Market

Industry/Entity Type

Retail

Contact Information for Business Card

Name : Devin Holt
Title : President
Phone : (800) 471-2960
Email: sleep@quilmora.com
Website: www.quilmora.com

Requirements
Must have
• Clean, Modern, Smooth
• Can use Blues/Greys
• On the other side without the information - have something simple like www.quilmora.com or our logo
Nice to have
• Surprise me
Should not have
• Nothing crazy, nothing cluttered

```html
<!DOCTYPE html>
<html lang="en">
<head>
<meta charset="utf-8">
<title>Quilmora Business Card – Devin Holt</title>
<link rel="stylesheet" href="https://fonts.googleapis.com/css2?family=Montserrat:wght@300;400;700&display=swap">
<style>
  :root {
    --page-bg: #eeeff0;
    --card-blue: #33a3d4;
    --tile-light: #cfe9f6;
    --tile-mid: #5db9e3;
    --tile-edge: #2a80b1;
    --icon-dark: #38a1d3;
    --text-light: #e6f4fb;
    --text-white: #ffffff;
    --watermark: rgba(255, 255, 255, 0.07);
  }
  * { margin: 0; padding: 0; box-sizing: border-box; }
  html, body { width: 1200px; height: 1200px; overflow: hidden; }
  body {
    background: var(--page-bg);
    font-family: "Montserrat", sans-serif;
    position: relative;
  }
  .card {
    position: absolute;
    left: 210px;
    width: 780px;
    height: 444px;
    background: var(--card-blue);
    overflow: hidden;
    box-shadow: 0 6px 18px rgba(0, 0, 0, 0.12);
  }
  .card-front { top: 130px; }
  .card-back { top: 640px; }

  .brand-name {
    position: absolute;
    left: 0; right: 0;
    top: 160px;
    text-align: center;
    font-weight: 300;
    font-size: 112px;
    line-height: 1;
    letter-spacing: 2px;
    color: var(--text-light);
  }
  .front-stripe {
    position: absolute;
    left: 0; right: 0; bottom: 0;
    height: 14px;
    display: flex;
  }
  .front-stripe span { flex: 1; }
  .front-stripe .light { background: var(--tile-light); }
  .front-stripe .mid { background: var(--tile-mid); }

  .icon-column {
    position: absolute;
    left: 0;
    top: 67px;
    width: 75px;
    border-right: 5px solid var(--tile-edge);
  }
  .icon-tile {
    height: 84px;
    display: flex;
    align-items: center;
    justify-content: center;
  }
  .icon-tile.light { background: var(--tile-light); }
  .icon-tile.mid { background: var(--tile-mid); }
  .icon-tile.light svg { fill: var(--icon-dark); }
  .icon-tile.mid svg { fill: var(--text-white); }
  .icon-tile svg { width: 24px; height: 24px; }

  .contact-list {
    position: absolute;
    left: 101px;
    top: 67px;
    list-style: none;
    font-size: 16px;
    font-weight: 400;
    color: var(--text-light);
  }
  .contact-list li {
    height: 84px;
    display: flex;
    flex-direction: column;
    justify-content: center;
    line-height: 1.3;
  }

  .brand-watermark {
    position: absolute;
    right: 24px;
    top: 140px;
    font-weight: 300;
    font-size: 112px;
    line-height: 1;
    letter-spacing: 2px;
    color: var(--watermark);
  }
  .person {
    position: absolute;
    right: 37px;
    top: 334px;
    text-align: center;
    color: var(--text-light);
  }
  .person-name {
    font-size: 41px;
    font-weight: 400;
    line-height: 1;
  }
  .person-name strong { font-weight: 700; }
  .person-title {
    margin-top: 14px;
    font-size: 22px;
    font-weight: 400;
    letter-spacing: 1.5px;
  }
</style>
</head>
<body>

  <section class="card card-front" aria-label="Card front">
    <div class="brand-name">quilmora</div>
    <div class="front-stripe">
      <span class="light"></span><span class="mid"></span><span class="light"></span><span class="mid"></span>
    </div>
  </section>

  <section class="card card-back" aria-label="Card back">
    <div class="brand-watermark" aria-hidden="true">quilmora</div>

    <div class="icon-column">
      <div class="icon-tile light">
        <svg viewBox="0 0 24 24" aria-hidden="true"><path d="M2 5h20v14H2z M3.5 6.5v.4l8.5 6 8.5-6v-.4z" fill-rule="evenodd"/></svg>
      </div>
      <div class="icon-tile mid">
        <svg viewBox="0 0 24 24" aria-hidden="true"><path d="M6.6 10.8a15.1 15.1 0 0 0 6.6 6.6l2.2-2.2c.3-.3.7-.4 1-.2 1.1.4 2.3.6 3.6.6.6 0 1 .4 1 1V20c0 .6-.4 1-1 1A17 17 0 0 1 3 4c0-.6.4-1 1-1h3.5c.6 0 1 .4 1 1 0 1.3.2 2.5.6 3.6.1.3 0 .7-.2 1z"/></svg>
      </div>
      <div class="icon-tile light">
        <svg viewBox="0 0 24 24" aria-hidden="true"><path d="M12 3 1.5 12H5v9h5.5v-6h3v6H19v-9h3.5z"/></svg>
      </div>
      <div class="icon-tile mid">
        <svg viewBox="0 0 24 24" aria-hidden="true"><path d="M12 2a10 10 0 1 0 0 20 10 10 0 0 0 0-20zm-1 17.9A8 8 0 0 1 4.2 10L9 14.8v1a2 2 0 0 0 2 2zm6.9-2.5a2 2 0 0 0-1.9-1.4h-1v-3a1 1 0 0 0-1-1H8v-2h2a1 1 0 0 0 1-1V7h2a2 2 0 0 0 2-2v-.4a8 8 0 0 1 2.9 12.8z"/></svg>
      </div>
    </div>

    <ul class="contact-list">
      <li>sleep@quilmora.com</li>
      <li>(800) 471-2960</li>
      <li><span>Your City Address</span><span>Street Location, NY City, USA</span></li>
      <li>www.quilmora.com</li>
    </ul>

    <div class="person">
      <div class="person-name">Devin <strong>Holt</strong></div>
      <div class="person-title">PRESIDENT</div>
    </div>
  </section>

</body>
</html>
```